Larkfield Air Business Card Design

Design new, 2 sides, business cards for a residential and light commercial heating, air conditioning contractor.

Target Market(s)

Homeowners, small businesses

Industry/Entity Type

Business

Contact Information for Business Card

Dominic Westerhall
Phone - 862-415-2736
Email
Address - PO box 518
Brightwater NJ 07912
Website - www.HarborBreezeLLC.example

Requirements
Must have
• logo, company colors, standard size with no die cut, so I can use nova stamp

```html
<!DOCTYPE html>
<html lang="en">
<head>
<meta charset="utf-8">
<title>Larkfield Air Business Card</title>
<link rel="stylesheet" href="https://fonts.googleapis.com/css2?family=Open+Sans:wght@400;600;700&display=swap">
<style>
  :root {
    --backdrop: #3b3431;
    --card-white: #f3f2f0;
    --card-black: #1d1c1c;
    --brand-red: #9b1c2e;
    --ink: #1f1f1f;
    --ink-soft: #333333;
    --white: #f4f4f4;
  }
  * { margin: 0; padding: 0; box-sizing: border-box; }
  html, body { width: 1200px; height: 844px; overflow: hidden; }
  body {
    background: var(--backdrop);
    font-family: "Open Sans", Arial, sans-serif;
    position: relative;
  }
  .card {
    position: absolute;
    width: 490px;
    height: 280px;
    top: 282px;
    border-radius: 3px;
    box-shadow: 0 10px 24px rgba(0,0,0,0.45);
  }
  .card--front { left: 80px; background: var(--card-white); color: var(--ink); }
  .card--back { left: 630px; background: var(--card-black); display: flex; align-items: center; justify-content: center; }

  .brand {
    display: flex;
    align-items: center;
    gap: 10px;
    font-weight: 700;
    letter-spacing: 0.5px;
    text-transform: uppercase;
    white-space: nowrap;
  }
  .brand__dot { width: 14px; height: 14px; border-radius: 50%; flex: none; }
  .card--front .brand {
    position: absolute;
    left: 210px;
    top: 58px;
    font-size: 30px;
    color: var(--brand-red);
  }
  .card--front .brand__dot { background: var(--brand-red); }
  .card--back .brand { font-size: 34px; color: var(--white); }
  .card--back .brand__dot { background: var(--white); }

  .person { position: absolute; left: 34px; top: 116px; }
  .person__name { font-size: 17px; font-weight: 700; color: var(--brand-red); line-height: 1.2; }
  .person__title { font-size: 15px; color: var(--ink); line-height: 1.3; }

  .address {
    position: absolute;
    right: 30px;
    top: 150px;
    text-align: right;
    font-size: 11.5px;
    line-height: 1.45;
    color: var(--ink-soft);
  }

  .contacts {
    position: absolute;
    left: 34px;
    bottom: 22px;
    list-style: none;
    font-size: 13px;
    line-height: 1.4;
    color: var(--ink);
  }
  .contacts li { display: flex; align-items: center; gap: 6px; }
  .contacts svg { width: 10px; height: 10px; fill: var(--brand-red); flex: none; }
</style>
</head>
<body>
  <section class="card card--front" aria-label="Business card front">
    <div class="brand"><span class="brand__dot"></span>Larkfield Air</div>

    <div class="person">
      <p class="person__name">Dominic Westerhall</p>
      <p class="person__title">Director</p>
    </div>

    <p class="address">PO box 518<br>Brightwater NJ 07912</p>

    <ul class="contacts">
      <li>
        <svg viewBox="0 0 10 10" aria-hidden="true"><path d="M1 3.5C1 2 2.5 1.5 5 1.5S9 2 9 3.5L7.5 4.5 6.8 3.4H3.2L2.5 4.5Z M2.5 5h5L9 9H1Z"/></svg>
        862-415-2736
      </li>
      <li>
        <svg viewBox="0 0 10 10" aria-hidden="true"><path d="M3 0.5h4a1 1 0 0 1 1 1v7a1 1 0 0 1-1 1H3a1 1 0 0 1-1-1v-7a1 1 0 0 1 1-1Zm0.6 1.2v5.5h2.8V1.7Z"/></svg>
        862-415-27914
      </li>
      <li>
        <svg viewBox="0 0 10 10" aria-hidden="true"><path d="M0.5 2h9v6h-9Zm1 1v0.3L5 5.6l3.5-2.3V3Z"/></svg>
        info@larkfieldair.example
      </li>
      <li>
        <svg viewBox="0 0 10 10" aria-hidden="true"><circle cx="5" cy="5" r="4.5"/></svg>
        www.LarkfieldAirLLC.example
      </li>
    </ul>
  </section>

  <section class="card card--back" aria-label="Business card back">
    <div class="brand"><span class="brand__dot"></span>Larkfield Air</div>
  </section>
</body>
</html>
```